we are an outdoor outlet in a country club that has a variety of outlets. The Club is called Meadowlark and is located in Cairo, Egypt. This garden menu will include cuisines from the Mediterranean, Asia and Texmex. we need a menu that is colorful and would fit an A3 size, back and front are to be used. Attached is the old menu currently in use (Garden Menu 2012.pdf is just for reference) and the new menu text for you to use is under the name Garden Menu Fall 2013
thank you.
Updates
Logo files have been uploaded for this project
Industry/Entity Type
Club
Look and feel
Each slider illustrates characteristics of the customer's brand and the style your logo design should communicate.

```html
<!DOCTYPE html>
<html lang="en">
<head>
<meta charset="utf-8">
<title>Garden Menu – Meadowlark Country Club</title>
<link rel="stylesheet" href="https://fonts.googleapis.com/css2?family=Poppins:wght@600;700&family=Questrial&family=Noto+Serif:wght@400;700&display=swap">
<style>
  :root {
    --paper: #f4e4c6;
    --paper-light: #f8eedb;
    --frame-green: #a9c73c;
    --ribbon-green: #b5cf2c;
    --ribbon-shadow: #7c8f1f;
    --brown: #5b3419;
    --brown-dark: #3b2210;
    --orange: #df5529;
    --lime-text: #cdd64a;
    --yellow-text: #f2d33b;
    --ink: #4b3a2b;
    --red-text: #c23a22;
    --white: #ffffff;
    --art-tone: #e4d3b2;
  }
  html, body {
    margin: 0;
    padding: 0;
    overflow: hidden;
    background: var(--paper);
  }
  .menu {
    position: relative;
    width: 848px;
    height: 1200px;
    overflow: hidden;
    background: radial-gradient(ellipse at 50% 40%, #f7e9cf 0%, var(--paper) 70%, #ecd6b0 100%);
    font-family: "Questrial", sans-serif;
    color: var(--ink);
  }
  .frame {
    position: absolute;
    left: 38px; top: 40px;
    width: 760px; height: 1108px;
    border: 3px solid var(--frame-green);
    box-sizing: border-box;
  }
  .header-band {
    position: absolute;
    left: 55px; top: 57px;
    width: 727px; height: 80px;
    background: var(--paper-light);
    opacity: .75;
  }
  .menu-title {
    position: absolute;
    left: 96px; top: 74px;
    margin: 0;
    font-family: "Poppins", sans-serif;
    font-weight: 700;
    font-size: 44px;
    line-height: 52px;
    letter-spacing: 0.5px;
    color: var(--brown);
  }
  .club-name {
    position: absolute;
    left: 552px; top: 82px;
    display: flex;
    align-items: center;
    gap: 10px;
  }
  .club-name .dot {
    width: 34px; height: 34px;
    border-radius: 50%;
    background: var(--frame-green);
  }
  .club-name span {
    font-family: "Questrial", sans-serif;
    font-size: 30px;
    color: var(--brown);
    line-height: 1;
  }

  .ribbon { position: absolute; background: var(--ribbon-green); }
  .ribbon-left { left: 0; top: 190px; width: 120px; height: 56px; }
  .ribbon-right { left: 740px; top: 233px; width: 108px; height: 57px; }
  .panel {
    position: absolute;
    border-radius: 14px;
    box-shadow: 2px 3px 6px rgba(0,0,0,.25);
  }
  .panel::after {
    content: "";
    position: absolute;
    inset: 6px;
    border: 1px dashed rgba(255,255,255,.55);
    border-radius: 10px;
  }
  .panel-asian { left: 68px; top: 203px; width: 340px; height: 345px; background: var(--brown); }
  .panel-texmex { left: 478px; top: 235px; width: 308px; height: 313px; background: var(--orange); }
  .tab {
    position: absolute;
    margin: 0;
    display: flex;
    align-items: center;
    justify-content: center;
    font-family: "Questrial", sans-serif;
    font-weight: 400;
    font-size: 30px;
    color: var(--white);
    box-shadow: 2px 3px 5px rgba(0,0,0,.3);
  }
  .tab-asian { left: 95px; top: 163px; width: 283px; height: 55px; background: var(--orange); }
  .tab-texmex { left: 456px; top: 205px; width: 284px; height: 57px; background: var(--brown); }
  .fold-left {
    position: absolute; left: 95px; top: 218px;
    width: 0; height: 0;
    border-top: 26px solid var(--brown-dark);
    border-left: 25px solid transparent;
  }
  .fold-right {
    position: absolute; left: 715px; top: 262px;
    width: 0; height: 0;
    border-top: 28px solid var(--ribbon-shadow);
    border-right: 25px solid transparent;
  }

  .section-heading {
    position: absolute;
    margin: 0;
    text-align: center;
    font-family: "Questrial", sans-serif;
    font-weight: 400;
    letter-spacing: 5px;
  }
  .heading-asian-main { left: 68px; top: 256px; width: 340px; font-size: 23px; color: var(--white); }
  .heading-texmex-main { left: 478px; top: 290px; width: 308px; font-size: 24px; line-height: 25px; color: var(--white); }
  .heading-salads { font-size: 19px; color: var(--brown); font-weight: 700; }
  .heading-salads-left { left: 98px; top: 564px; width: 283px; }
  .heading-salads-right { left: 460px; top: 564px; width: 280px; }
  .heading-desserts {
    left: 360px; top: 806px; width: 140px;
    font-size: 27px; letter-spacing: 0; color: var(--brown);
  }

  .divider { position: absolute; height: 1px; background: var(--frame-green); }
  .divider .dot {
    position: absolute;
    left: 50%; top: -7px;
    width: 14px; height: 14px;
    margin-left: -7px;
    border-radius: 50%;
    background: var(--frame-green);
  }

  .item { position: absolute; }
  .item-row {
    display: flex;
    justify-content: space-between;
    align-items: baseline;
    font-size: 11.5px;
    line-height: 13px;
    text-transform: uppercase;
  }
  .item-desc {
    margin: 0;
    font-family: "Noto Serif", serif;
    font-size: 8.6px;
    line-height: 11px;
  }
  .asian .item-row { color: var(--lime-text); }
  .asian .item-desc { color: var(--white); }
  .texmex .item-row { color: var(--yellow-text); text-transform: none; }
  .texmex .item-desc { color: var(--white); }
  .light .item-row { color: var(--ink); }
  .light .item-desc { color: var(--red-text); }
  .dessert .item-row { font-size: 12px; }
  .dessert .item-desc { font-weight: 700; }
  .dessert.bold-ink .item-desc { color: var(--brown-dark); }

  .badge {
    position: absolute;
    left: 376px; top: 1060px;
    width: 92px; height: 92px;
    border-radius: 50%;
    background: var(--orange);
    border: 2px solid var(--paper-light);
    box-sizing: border-box;
    display: flex;
    align-items: center;
    justify-content: center;
    text-align: center;
    font-family: "Noto Serif", serif;
    font-weight: 700;
    font-size: 7.4px;
    line-height: 9px;
    color: var(--white);
  }

  .art {
    position: absolute;
    border-radius: 40%;
    background: radial-gradient(ellipse at center, #f1e6d2 0%, var(--art-tone) 60%, rgba(228,211,178,0) 100%);
  }
</style>
</head>
<body>
<main class="menu">
  <div class="frame"></div>
  <div class="header-band"></div>
  <h1 class="menu-title">GARDEN MENU</h1>
  <div class="club-name"><div class="dot"></div><span>Meadowlark</span></div>

  <!-- Asian corner -->
  <div class="ribbon ribbon-left"></div>
  <div class="panel panel-asian"></div>
  <h2 class="tab tab-asian">ASIAN CORNER</h2>
  <div class="fold-left"></div>
  <h3 class="section-heading heading-asian-main">main courses</h3>
  <div class="divider" style="left:98px;top:299px;width:283px"><span class="dot"></span></div>

  <div class="item asian" style="left:98px;top:326px;width:283px">
    <div class="item-row"><span>Murgh Chicken Makhni</span><span>00.00</span></div>
    <p class="item-desc">Chicken cubes in a rich creamy tomato sauce<br>seasoned with garam masala<br>Choice of side: <b>vegetable korma</b> or <b>curd</b></p>
  </div>
  <div class="item asian" style="left:98px;top:384px;width:283px">
    <div class="item-row"><span>Chicken Tandoori</span><span>00.00</span></div>
    <p class="item-desc">Grilled chicken cubes with tandoori spices<br>served with basmati rice</p>
  </div>
  <div class="item asian" style="left:98px;top:430px;width:283px">
    <div class="item-row"><span>Thai Coconut Curry Shrimp</span><span>00.00</span></div>
    <p class="item-desc">Sautéed shrimp tossed with curry<br>and coconut milk served with jasmine rice</p>
  </div>
  <div class="item asian" style="left:98px;top:476px;width:283px">
    <div class="item-row"><span>Mongolian Beef</span><span>00.00</span></div>
    <p class="item-desc">Soy marinated beef with oyster sauce<br>and vegetables served with egg noodles</p>
  </div>

  <!-- Tex Mex -->
  <div class="ribbon ribbon-right"></div>
  <div class="panel panel-texmex"></div>
  <h2 class="tab tab-texmex">TEX MEX</h2>
  <div class="fold-right"></div>
  <h3 class="section-heading heading-texmex-main">main courses<br>&amp; sandwiches</h3>
  <div class="divider" style="left:506px;top:356px;width:268px"><span class="dot"></span></div>

  <div class="item texmex" style="left:506px;top:364px;width:268px">
    <div class="item-row"><span>Cheeseburger</span><span>00.00</span></div>
    <p class="item-desc">House made lean beef burger<br>topped with cheddar cheese</p>
  </div>
  <div class="item texmex" style="left:506px;top:410px;width:268px">
    <div class="item-row"><span>Mushroom Burger</span><span>00.00</span></div>
    <p class="item-desc">Beef burger with sautéed mushroom,<br>caramelized onion, and provolone cheese</p>
  </div>
  <div class="item texmex" style="left:506px;top:457px;width:268px">
    <div class="item-row"><span>Crispy Chicken Wrap</span><span>00.00</span></div>
    <p class="item-desc">Crisp fried chicken wrap with a ranch dressing</p>
  </div>
  <div class="item texmex" style="left:506px;top:491px;width:268px">
    <div class="item-row"><span>Fajita (Chicken, Beef, Combo)</span><span>00.00</span></div>
    <p class="item-desc">Pan seared meat or chicken with onion and<br>bell pepper served with sour cream, guacamole, salsa</p>
  </div>

  <!-- Salads & appetizers -->
  <h3 class="section-heading heading-salads heading-salads-left">salads &amp; appetizer</h3>
  <div class="divider" style="left:98px;top:603px;width:283px"><span class="dot"></span></div>
  <h3 class="section-heading heading-salads heading-salads-right">salads &amp; appetizer</h3>
  <div class="divider" style="left:460px;top:603px;width:283px"><span class="dot"></span></div>

  <div class="item light" style="left:98px;top:624px;width:283px">
    <div class="item-row"><span>Chicken Wasabi Salad</span><span>00.00</span></div>
    <p class="item-desc">Diced chicken with a mayo wasabi<br>dressing on top of shredded lettuce</p>
  </div>
  <div class="item light" style="left:98px;top:670px;width:283px">
    <div class="item-row"><span>Chicken Sesame Noodle Salad</span><span>00.00</span></div>
    <p class="item-desc">Sesame crusted chicken with glass noodles<br>tossed with sweet chili, soy sauce, and lemongrass</p>
  </div>
  <div class="item light" style="left:98px;top:716px;width:283px">
    <div class="item-row"><span>Spring Rolls</span><span>00.00</span></div>
    <p class="item-desc">Vegetable spring rolls served with house made<br>sweet and sour dip</p>
  </div>
  <div class="item light" style="left:98px;top:762px;width:283px">
    <div class="item-row"><span>Indian Samosa</span><span>00.00</span></div>
    <p class="item-desc">Fried dough parcels filled with<br>vegetables and spices</p>
  </div>

  <div class="item light" style="left:460px;top:624px;width:280px">
    <div class="item-row"><span>Caesar Salad</span><span>00.00</span></div>
    <p class="item-desc">Iceberg lettuce with Caesar dressing with<br>grated Parmesan cheese and croutons</p>
  </div>
  <div class="item light" style="left:460px;top:670px;width:283px">
    <div class="item-row"><span>Taco Salad 42</span><span>00.00</span></div>
    <p class="item-desc">Chicken breast, beans, sour cream, guacamole,<br>tomato, corn, lettuce, olives, chives, vinaigrette</p>
  </div>
  <div class="item light" style="left:460px;top:716px;width:280px">
    <div class="item-row"><span>Nachos</span><span>00.00</span></div>
    <p class="item-desc">Topped with chili, melted cheese, beans</p>
  </div>
  <div class="item light" style="left:460px;top:751px;width:280px">
    <div class="item-row"><span>Chicken Quesadilla</span><span>00.00</span></div>
    <p class="item-desc">served with guacamole, salsa, and sour cream</p>
  </div>

  <!-- Desserts -->
  <h3 class="section-heading heading-desserts">DESSERTS</h3>
  <div class="divider" style="left:300px;top:852px;width:250px"><span class="dot"></span></div>

  <div class="item light dessert" style="left:98px;top:874px;width:283px"><div class="item-row"><span>Mix Berries Cheesecake</span><span>00.00</span></div></div>
  <div class="item light dessert" style="left:98px;top:903px;width:283px"><div class="item-row"><span>Crème Brulee</span><span>00.00</span></div></div>
  <div class="item light dessert" style="left:98px;top:932px;width:283px"><div class="item-row"><span>Chocolate Caramel Cake</span><span>00.00</span></div></div>
  <div class="item light dessert" style="left:98px;top:960px;width:283px"><div class="item-row"><span>Warm Chocolate Fondant</span><span>00.00</span></div></div>
  <div class="item light dessert" style="left:98px;top:989px;width:283px"><div class="item-row"><span>Baked Apple Tart Tatin</span><span>00.00</span></div></div>
  <div class="item light dessert" style="left:98px;top:1018px;width:283px"><div class="item-row"><span>Tiramisu</span><span>00.00</span></div></div>
  <div class="item light dessert" style="left:98px;top:1047px;width:283px"><div class="item-row"><span>Pumpkin Pie Flan</span><span>00.00</span></div></div>
  <div class="item light dessert" style="left:98px;top:1075px;width:283px"><div class="item-row"><span>Mixed Berries Granola Yoghurt</span><span>00.00</span></div></div>

  <div class="item light dessert" style="left:460px;top:874px;width:283px">
    <div class="item-row"><span>Vanilla Ice Cream</span><span>00.00</span></div>
    <p class="item-desc">Profiterole with dark and white chocolate sauce</p>
  </div>
  <div class="item light dessert" style="left:460px;top:915px;width:280px">
    <div class="item-row"><span>Caramelized Banana</span><span>00.00</span></div>
    <p class="item-desc">With deep fried ice cream</p>
  </div>
  <div class="item light dessert" style="left:460px;top:956px;width:283px">
    <div class="item-row"><span>Baklava</span><span>00.00</span></div>
    <p class="item-desc">With nuts and sugar syrup</p>
  </div>
  <div class="item light dessert bold-ink" style="left:460px;top:996px;width:280px">
    <div class="item-row"><span>Shot Glass Sampler</span><span>00.00</span></div>
    <p class="item-desc">Tiramisu, chocolate crisp mousse,<br>pear with sabayon</p>
  </div>
  <div class="item light dessert" style="left:460px;top:1049px;width:283px"><div class="item-row"><span>Ice Cream by Scoop</span><span>00.00</span></div></div>

  <div class="badge">PRICES ARE<br>SUBJECT TO<br>12% SERVICE<br>CHARGE &amp;<br>10% SALES TAX</div>

  <!-- illustration areas -->
  <div class="art" role="img" aria-label="Sketch of garlic bulbs" style="left:688px;top:158px;width:98px;height:46px"></div>
  <div class="art" role="img" aria-label="Sketch of an ear of corn" style="left:418px;top:228px;width:100px;height:58px;background:linear-gradient(160deg,#d9c29a,#bfa274)"></div>
  <div class="art" role="img" aria-label="Sketch of a wok with stir-fried food" style="left:330px;top:492px;width:136px;height:64px"></div>
  <div class="art" role="img" aria-label="Sketch of a slice of layered cake" style="left:276px;top:796px;width:80px;height:60px"></div>
  <div class="art" role="img" aria-label="Sketch of mushrooms" style="left:662px;top:782px;width:106px;height:60px"></div>
</main>
</body>
</html>
```